BrivoTerna. Lantern of the Steady Harvest. Business card

Professional business card for BrivoTerna (Lantern of the Steady Harvest)
My rationale: Strategy-> Execution-> Results-> Value that lead to the BrivoTerna name: We put the Lantern of the Steady Harvest.
We deliver value to our customers helping them at defining a good strategy (cyan arrow). 90% of well formulated strategies fail due to poor execution so we also consider strategical execution very important (green arrow). Due to the execution we obtain the results (blue arrow). Finally, the results provide feedback to redefine strategy, and the new strategy has to be executed and new results obtained providing new feedback and on and on. It's like a wheel that finally, must create corporate value: value for shareholders, staholders, employees, providers...-

Target Market(s)

CEOs and steering comitees , invewrnent funds

Industry/Entity Type

Business Consultant

Contact Information for Business Card

Teodoro Vinsquel
CEO & Founder
teodoro.vinsquel@brivoterna-example.com
Mobile: +34 655.803.912
www.brivoterna-example.com

Colors

Designer to choose colors to be used in the design.

Requirements
Nice to have
• Nice to hace the words: Strategy, execution, results
• Nice to vave the claim: Lantern of the Steady Harvest
• The three colors should be shown:
• cyan for STRATEGY
• green for EXECUTION
• blue for RESULTS
Should not have
• Complete black background

```html
<!DOCTYPE html>
<html lang="en">
<head>
<meta charset="utf-8">
<title>BrivoTerna – Business Card</title>
<link href="https://fonts.googleapis.com/css2?family=Fira+Sans:wght@400;600;700&display=swap" rel="stylesheet">
<style>
  :root {
    --navy: #27348b;
    --deep-blue: #243a8c;
    --deep-blue-dark: #1c2d78;
    --green: #8dc63f;
    --cyan: #2ba0d9;
    --ink: #1f2533;
    --paper: #ffffff;
    --backdrop: #e9e9e7;
  }
  * { box-sizing: border-box; margin: 0; padding: 0; }
  html, body {
    width: 1200px; height: 859px; overflow: hidden;
    background: var(--backdrop);
    font-family: "Fira Sans", sans-serif;
  }
  .canvas { position: relative; width: 1200px; height: 859px; }
  .card {
    position: absolute; top: 288px; width: 501px; height: 285px;
    box-shadow: 0 6px 18px rgba(0,0,0,.18);
    overflow: hidden;
  }
  .card-front { left: 59px; background: var(--paper); }
  .card-back {
    left: 639px;
    background: linear-gradient(135deg, var(--deep-blue), var(--deep-blue-dark));
  }
  .brand-name {
    font-weight: 700; letter-spacing: -0.5px; line-height: 1;
  }
  .card-front .brand-name {
    position: absolute; left: 25px; top: 24px;
    font-size: 40px; color: var(--navy);
  }
  .holder { position: absolute; left: 25px; top: 106px; }
  .holder-name {
    font-size: 17px; font-weight: 700; color: var(--navy);
    text-transform: uppercase; letter-spacing: .2px;
  }
  .holder-role { font-size: 12.5px; color: var(--green); margin-top: 1px; }
  .contact-list {
    position: absolute; left: 25px; top: 160px; list-style: none;
    font-size: 12px; color: var(--ink);
  }
  .contact-list li { display: flex; align-items: center; height: 17px; }
  .contact-list svg { width: 11px; height: 11px; margin-right: 7px; flex: none; }
  .divider {
    position: absolute; left: 25px; top: 228px; width: 223px; height: 1px;
    background: var(--green);
  }
  .claim {
    position: absolute; left: 25px; top: 247px;
    font-size: 12.5px; color: var(--ink); text-transform: uppercase;
  }
  .back-brand {
    position: absolute; left: 0; right: 0; top: 100px;
    display: flex; flex-direction: column; align-items: flex-end;
    padding-right: 60px;
  }
  .brand-dot {
    width: 34px; height: 34px; border-radius: 50%;
    background: var(--cyan); margin-right: 107px; margin-bottom: 22px;
  }
  .card-back .brand-name { font-size: 44px; color: var(--paper); }
  .pillars {
    margin-top: 10px; font-size: 13.5px; font-weight: 600;
    text-transform: uppercase; color: var(--paper);
  }
  .pillars .execution { color: var(--green); }
  .pillars .results { color: var(--cyan); }
  .pillars .sep { color: var(--paper); margin: 0 3px; }
</style>
</head>
<body>
<main class="canvas">
  <section class="card card-front" aria-label="Business card front">
    <div class="brand-name">BrivoTerna</div>
    <div class="holder">
      <div class="holder-name">Teodoro Vinsquel</div>
      <div class="holder-role">CEO &amp; Founder</div>
    </div>
    <ul class="contact-list">
      <li>
        <svg viewBox="0 0 12 12" aria-hidden="true"><circle cx="6" cy="6" r="5.2" fill="none" stroke="#2ba0d9" stroke-width="1"/><path d="M4 3.5c0 2.5 2 4.5 4.5 4.5l.5-1.2-1.3-.6-.6.6c-.8-.4-1.3-.9-1.7-1.7l.6-.6-.6-1.3z" fill="#2ba0d9"/></svg>
        +34 655.803.912
      </li>
      <li>
        <svg viewBox="0 0 12 12" aria-hidden="true"><rect x="1" y="2.5" width="10" height="7" fill="none" stroke="#2ba0d9" stroke-width="1"/><path d="M1 2.5l5 4 5-4" fill="none" stroke="#2ba0d9" stroke-width="1"/></svg>
        teodoro.vinsquel@brivoterna-example.com
      </li>
      <li>
        <svg viewBox="0 0 12 12" aria-hidden="true"><circle cx="6" cy="6" r="5.2" fill="#2ba0d9"/><path d="M1 6h10M6 .8c-2 2.8-2 7.6 0 10.4M6 .8c2 2.8 2 7.6 0 10.4" fill="none" stroke="#fff" stroke-width=".7"/></svg>
        www.brivoterna-example.com
      </li>
    </ul>
    <div class="divider"></div>
    <div class="claim">Lantern of the Steady Harvest</div>
  </section>

  <section class="card card-back" aria-label="Business card back">
    <div class="back-brand">
      <div class="brand-dot"></div>
      <div class="brand-name">BrivoTerna</div>
      <div class="pillars">
        <span class="strategy">Strategy</span><span class="sep">|</span><span class="execution">Execution</span><span class="sep">|</span><span class="results">Results</span>
      </div>
    </div>
  </section>
</main>
</body>
</html>
```